Tandem Hearth Works Pty Ltd

We need business cards for a company based in Perth, we install, service and maintain fire equipment.
On the front we want a great design with our logo and a small spot for our full company name, general company email address and office number. On the back we need space for our name, title, mobile number and email address on the back.

Target Market(s)

Facility managers and commercial/industrial building owners/occupiers.

Contact Information for Business Card

Font styles to use
Sans Serif

Requirements
Must have
• Please only submit 5 of your best samples.
Darker tones are preferred.
Nice to have
• We want to use, black, red and grey. Keep it modern and clean.
I've attached the company logo and a sample of a boarder we use on our emergency plans.
Should not have
• No preference. Let the designer choose.

```html
<!DOCTYPE html>
<html lang="en">
<head>
<meta charset="utf-8">
<title>Tandem Hearth Works – Business Cards</title>
<link rel="stylesheet" href="https://fonts.googleapis.com/css2?family=Montserrat:wght@400;500;800&display=swap">
<style>
  :root {
    --bg: #2a2624;
    --card: #161616;
    --red: #ff1a1a;
    --red-text: #ee2a2f;
    --grey: #8a8a8a;
    --white: #f2f2f2;
    --rule: #6a6a6a;
  }
  * { box-sizing: border-box; margin: 0; padding: 0; }
  html, body { width: 1200px; height: 842px; overflow: hidden; }
  body {
    background: var(--bg);
    font-family: "Montserrat", Arial, sans-serif;
    position: relative;
  }
  .card {
    position: absolute;
    width: 520px;
    height: 298px;
    background: var(--card);
    box-shadow: 0 14px 30px rgba(0,0,0,.55);
    overflow: hidden;
  }
  .card--personal { left: 50px; top: 400px; }
  .card--company { left: 630px; top: 150px; }
  .band { position: absolute; left: 0; width: 100%; height: 14px; display: block; }
  .band--top { top: 0; }
  .band--bottom { bottom: 0; transform: scaleX(-1); }

  .brand {
    position: absolute; top: 58px; left: 0; width: 100%;
    text-align: center;
    color: var(--red-text);
    font-weight: 800;
    font-size: 64px;
    letter-spacing: 2px;
    line-height: 1;
  }
  .person { position: absolute; top: 148px; left: 0; width: 100%; text-align: center; }
  .person__name { color: var(--red-text); font-weight: 800; font-size: 22px; letter-spacing: .5px; }
  .person__title { color: var(--white); font-size: 16px; font-weight: 500; margin-top: 2px; }
  .person__rule { width: 200px; height: 1px; background: var(--rule); margin: 10px auto 12px; }
  .contacts { display: flex; justify-content: center; gap: 22px; color: var(--white); font-size: 16px; }
  .contact { display: flex; align-items: center; gap: 7px; }
  .contact svg { display: block; }

  .company { position: absolute; top: 70px; left: 0; width: 100%; text-align: center; }
  .company__name { color: var(--red-text); font-weight: 800; font-size: 21px; line-height: 1.15; text-transform: uppercase; }
  .company__phone { color: var(--white); font-weight: 800; font-size: 27px; margin-top: 14px; }
  .company .contacts { font-size: 14px; margin-top: 12px; }
</style>
</head>
<body>

<svg width="0" height="0" style="position:absolute">
  <defs>
    <g id="stripe-band">
      <rect x="0" y="0" width="520" height="14" fill="#8a8a8a"/>
      <polygon points="0,0 40,0 20,14 0,14" fill="#ff1a1a"/>
      <polygon points="170,0 330,0 310,14 150,14" fill="#ff1a1a"/>
      <polygon points="440,0 520,0 520,14 420,14" fill="#ff1a1a"/>
    </g>
  </defs>
</svg>

<section class="card card--personal">
  <svg class="band band--top" viewBox="0 0 520 14" preserveAspectRatio="none"><use href="#stripe-band"/></svg>
  <div class="brand">THW</div>
  <div class="person">
    <div class="person__name">MARCUS ELLERY</div>
    <div class="person__title">Managing Director</div>
    <div class="person__rule"></div>
    <div class="contacts">
      <span class="contact">
        <svg width="12" height="18" viewBox="0 0 12 18"><rect x="1" y="1" width="10" height="16" rx="2" fill="none" stroke="#ee2a2f" stroke-width="2"/><rect x="4" y="13" width="4" height="1.6" fill="#ee2a2f"/></svg>
        789.4410.2283
      </span>
      <span class="contact">
        <svg width="20" height="14" viewBox="0 0 20 14"><rect width="20" height="14" fill="#ee2a2f"/><polyline points="0,0 10,8 20,0" fill="none" stroke="#161616" stroke-width="1.6"/></svg>
        marcus@thw.com
      </span>
    </div>
  </div>
  <svg class="band band--bottom" viewBox="0 0 520 14" preserveAspectRatio="none"><use href="#stripe-band"/></svg>
</section>

<section class="card card--company">
  <svg class="band band--top" viewBox="0 0 520 14" preserveAspectRatio="none"><use href="#stripe-band"/></svg>
  <div class="company">
    <div class="company__name">Tandem Hearth<br>Works Pty Ltd</div>
    <div class="company__phone">789.5520.6614</div>
    <div class="contacts">
      <span class="contact">
        <svg width="18" height="12" viewBox="0 0 20 14"><rect width="20" height="14" fill="#ee2a2f"/><polyline points="0,0 10,8 20,0" fill="none" stroke="#161616" stroke-width="1.6"/></svg>
        info@thw.com
      </span>
      <span class="contact">
        <svg width="14" height="14" viewBox="0 0 14 14"><circle cx="7" cy="7" r="6" fill="none" stroke="#ee2a2f" stroke-width="1.6"/><ellipse cx="7" cy="7" rx="2.6" ry="6" fill="none" stroke="#ee2a2f" stroke-width="1.2"/><line x1="1" y1="7" x2="13" y2="7" stroke="#ee2a2f" stroke-width="1.2"/></svg>
        www.thw.com
      </span>
    </div>
  </div>
  <svg class="band band--bottom" viewBox="0 0 520 14" preserveAspectRatio="none"><use href="#stripe-band"/></svg>
</section>

</body>
</html>
```